Unique Business Card Design

Unique Business Card design for our orthotic and prosthetic company. Our logo is on our website, color is light blue. Unique shape (artificial leg shaped, vertical, etc..) preferred. Logo, business name, individual name and basic demographics needed.

Industry/Entity Type

Business

Contact Information for Business Card

Logo, Industry, Phone # Logo, "Prosthetic & Orthotic Services" Place to add individual name and contact info

Colors
cee9f5

Requirements
Must have
• The icon must be there, placement of "Prosthetic & Orthotic Services" can be moved
Nice to have
• Like the mix of light blue, and a little darker blue. One design included the icons from my website which was a nice touch

```html
<!DOCTYPE html>
<html lang="en">
<head>
<meta charset="utf-8">
<title>Limbwell Inc. Business Card</title>
<link rel="stylesheet" href="https://fonts.googleapis.com/css2?family=Open+Sans:wght@400;600&family=Roboto:wght@400;500;700&display=swap">
<style>
  :root {
    --brand-blue: #0b5aa8;
    --brand-blue-deep: #08509a;
    --brand-blue-light: #1a6dbd;
    --sky: #cee9f5;
    --ink-grey: #5a5a5a;
    --rule-grey: #d4d7db;
    --paper: #ffffff;
    --backdrop: #e8ebee;
  }
  html, body {
    margin: 0;
    padding: 0;
    width: 1200px;
    height: 1000px;
    overflow: hidden;
    background: var(--backdrop);
  }
  .canvas {
    position: relative;
    width: 1200px;
    height: 1000px;
  }
  .card {
    position: absolute;
    left: 220px;
    width: 760px;
    border-radius: 28px;
    overflow: hidden;
    box-shadow: 0 6px 18px rgba(0,0,0,0.18);
  }
  /* Front */
  .card-front {
    top: 50px;
    height: 433px;
    background: linear-gradient(120deg, var(--brand-blue-deep) 0%, var(--brand-blue) 55%, var(--brand-blue-light) 100%);
    color: var(--paper);
  }
  .front-mark {
    position: absolute;
    left: 122px;
    top: 147px;
    width: 140px;
    height: 140px;
    border-radius: 50%;
    background: var(--paper);
  }
  .front-name {
    position: absolute;
    left: 278px;
    top: 168px;
    font-family: "Open Sans", sans-serif;
    font-weight: 600;
    font-size: 40px;
    line-height: 1;
    letter-spacing: -0.5px;
    margin: 0;
  }
  .front-rule {
    position: absolute;
    left: 283px;
    top: 216px;
    width: 352px;
    height: 4px;
    background: var(--paper);
  }
  .front-tagline {
    position: absolute;
    left: 298px;
    top: 231px;
    font-family: "Open Sans", sans-serif;
    font-weight: 400;
    font-size: 21px;
    margin: 0;
  }
  .front-web {
    position: absolute;
    left: 0;
    width: 760px;
    top: 374px;
    text-align: center;
    font-family: "Open Sans", sans-serif;
    font-size: 16px;
    margin: 0;
  }
  /* Back */
  .card-back {
    top: 524px;
    height: 436px;
    background: var(--paper);
  }
  .back-mark {
    position: absolute;
    left: 43px;
    top: 171px;
    width: 94px;
    height: 94px;
    border-radius: 50%;
    background: var(--brand-blue);
  }
  .back-name {
    position: absolute;
    left: 150px;
    top: 186px;
    font-family: "Open Sans", sans-serif;
    font-weight: 600;
    font-size: 26px;
    line-height: 1;
    color: var(--brand-blue);
    margin: 0;
  }
  .back-rule {
    position: absolute;
    left: 152px;
    top: 218px;
    width: 240px;
    height: 3px;
    background: var(--brand-blue);
  }
  .back-tagline {
    position: absolute;
    left: 164px;
    top: 226px;
    font-family: "Open Sans", sans-serif;
    font-size: 14px;
    color: var(--brand-blue);
    margin: 0;
  }
  .divider {
    position: absolute;
    left: 418px;
    top: 94px;
    width: 1px;
    height: 248px;
    background: var(--rule-grey);
  }
  .contact {
    position: absolute;
    left: 442px;
    top: 90px;
    font-family: "Roboto", sans-serif;
    color: var(--ink-grey);
    font-size: 16.5px;
    line-height: 22px;
  }
  .contact p { margin: 0; }
  .person-name {
    font-weight: 700;
    font-size: 22px;
    color: var(--brand-blue);
    line-height: 28px;
  }
  .person-title { margin-bottom: 14px !important; }
  .company { color: var(--brand-blue); }
  .address { margin-bottom: 12px !important; }
  .contact-line {
    display: flex;
    align-items: center;
    gap: 6px;
    line-height: 24.5px;
  }
  .contact-line svg { width: 13px; height: 13px; flex: none; fill: var(--brand-blue); }
  .web-highlight { color: var(--brand-blue); }
  .back-footer-line {
    position: absolute;
    left: 0;
    bottom: 20px;
    width: 100%;
    height: 2px;
    background: var(--rule-grey);
  }
  .back-footer-band {
    position: absolute;
    left: 0;
    bottom: 0;
    width: 100%;
    height: 17px;
    background: var(--brand-blue);
  }
</style>
</head>
<body>
<main class="canvas">
  <section class="card card-front" aria-label="Card front">
    <div class="front-mark"></div>
    <h1 class="front-name">LIMBWELL INC.</h1>
    <div class="front-rule"></div>
    <p class="front-tagline">Prosthetic &amp; Orthotic Services</p>
    <p class="front-web">www.limbwellinc.com</p>
  </section>

  <section class="card card-back" aria-label="Card back">
    <div class="back-mark"></div>
    <h2 class="back-name">LIMBWELL INC.</h2>
    <div class="back-rule"></div>
    <p class="back-tagline">Prosthetic &amp; Orthotic Services</p>

    <div class="divider"></div>

    <div class="contact">
      <p class="person-name">Mara Castellan</p>
      <p class="person-title">CO LPO</p>
      <p class="company">LIMBWELL INC.</p>
      <p class="address">2190 West 14th Street<br>Riverton, NY 11000</p>
      <p class="contact-line">
        <svg viewBox="0 0 16 16" aria-hidden="true"><path d="M4 0h8a1 1 0 0 1 1 1v14a1 1 0 0 1-1 1H4a1 1 0 0 1-1-1V1a1 1 0 0 1 1-1zm1 2v10h6V2zm3 11a1 1 0 1 0 0 2 1 1 0 0 0 0-2z"/></svg>
        845-5550142
      </p>
      <p class="contact-line">
        <svg viewBox="0 0 16 16" aria-hidden="true"><path d="M3.6 1.2l2.2 2.6-1.3 1.8c.9 2 2.6 3.8 4.6 4.8l1.9-1.3 2.6 2.2-1.4 2.6C6.9 13.6 2.3 9 1.1 3z"/></svg>
        (718) 555-0170
      </p>
      <p class="contact-line">
        <svg viewBox="0 0 16 16" aria-hidden="true"><path d="M4 1h7l1 1v3H4zM2 6h12a1 1 0 0 1 1 1v5h-3v3H4v-3H1V7a1 1 0 0 1 1-1zm3 4v4h6v-4z"/></svg>
        (718) 555-0193
      </p>
      <p class="contact-line">
        <svg viewBox="0 0 16 16" aria-hidden="true"><path d="M1 3h14v1L8 9 1 4zm0 2.4l7 5 7-5V13H1z"/></svg>
        Mcastellan@limbwellinc.com
      </p>
      <p class="contact-line">
        <svg viewBox="0 0 16 16" aria-hidden="true"><path d="M8 1a7 7 0 1 0 0 14A7 7 0 0 0 8 1zm0 1.3c.8.8 1.5 2.2 1.8 3.9H6.2C6.5 4.5 7.2 3.1 8 2.3zM2.4 7.4h2.6a12 12 0 0 0 0 1.2H2.4a5.6 5.6 0 0 1 0-1.2zm3.8 0h3.6a11 11 0 0 1 0 1.2H6.2a11 11 0 0 1 0-1.2zm4.8 0h2.6a5.6 5.6 0 0 1 0 1.2H11a12 12 0 0 0 0-1.2zM6.2 9.8h3.6c-.3 1.7-1 3.1-1.8 3.9-.8-.8-1.5-2.2-1.8-3.9z"/></svg>
        <span>www.<span class="web-highlight">limbwellinc</span>.net</span>
      </p>
    </div>

    <div class="back-footer-line"></div>
    <div class="back-footer-band"></div>
  </section>
</main>
</body>
</html>
```